Brightline Energy Product Distribution Brochure

We are looking to have our current brochure for our customers completely redesigned...the idea is to present the relevant information in an attractive way . Our website is brightlineenergyco.example where you can find more information about us. We have included a file with a rough idea of the page order and what each should include but feel free to adapt based on design. The example provided is only for context and doesnt have to be maintained. We will be using the brochure both digitally and in print form. As long as it reads easily and is eye catching, the design can be horizontal or vertical.Final deliverable should be indesign file.

"Our Brands" page: should be limited to one page (space being enough) where it has the header for each one (for example diesel generators) space for one or two lines of text and then the corresponding logos for each of the five categories
Updates

For those asking: the "our brands" page should be a single page layout where there is a header with the corresponding section and space for maybe one line of text followed by the two logos for that category. Each of the product pages should be similar in fashion to the one in the document attached: a photo of the product with some white space and space for the text to be included. We will be posting additional examples today

Target Market(s)

We want to present it to customers both digitally and in print so they can see our products

Industry/Entity Type

Power Generation

Font styles to use
Serif

Requirements
Must have
• Eye catching and able to present the information in a presentable fashion. Rest is up to you.
Nice to have
• Should incorporate the colors of our logo but can also add other depending on design

```html
<!DOCTYPE html>
<html lang="en">
<head>
<meta charset="utf-8">
<title>Brightline Energy – Brochure Inside Pages</title>
<link href="https://fonts.googleapis.com/css2?family=Montserrat:ital,wght@1,300&family=Raleway:wght@300;400;500;700;800&display=swap" rel="stylesheet">
<style>
  :root {
    --brand-yellow: #fccb05;
    --brand-yellow-deep: #efbf0c;
    --ink: #1d1d1b;
    --label-grey: #6b6b6b;
    --paper: #ffffff;
    --board: #ffffff;
    --photo-light: #e6e6e6;
    --photo-dark: #2b2b2b;
  }
  * { margin: 0; padding: 0; box-sizing: border-box; }
  html, body { width: 1200px; height: 1200px; overflow: hidden; background: var(--board); }
  .board { position: relative; width: 1200px; height: 1200px; }

  .spread-label {
    position: absolute; top: 136px;
    font-family: "Montserrat", sans-serif; font-style: italic; font-weight: 300;
    font-size: 24px; color: var(--label-grey); letter-spacing: 0.5px;
  }

  .page-holder { position: absolute; top: 216px; width: 547px; height: 776px; box-shadow: 0 30px 40px rgba(0,0,0,0.12); }
  .page {
    position: absolute; top: 0; left: 0; width: 684px; height: 970px;
    transform: scale(0.8); transform-origin: 0 0;
    background: var(--paper); overflow: hidden;
    font-family: "Raleway", sans-serif; color: var(--ink);
  }
  .page-art { position: absolute; inset: 0; width: 684px; height: 970px; }

  .section-tab { position: absolute; left: 0; top: 43px; width: 58px; height: 12px; background: var(--brand-yellow); }
  .section-name { position: absolute; left: 68px; top: 41px; font-size: 14px; font-weight: 400; letter-spacing: 0.2px; }

  .brand { position: absolute; right: 62px; top: 44px; display: flex; align-items: center; gap: 7px; }
  .brand-mark { width: 20px; height: 20px; background: var(--brand-yellow); }
  .brand-name { font-size: 12px; font-weight: 500; color: var(--ink); letter-spacing: 0.3px; }

  .page-title { position: absolute; left: 58px; top: 113px; font-size: 44px; font-weight: 300; letter-spacing: -0.5px; white-space: nowrap; }
  .block-heading { position: absolute; left: 58px; top: 194px; font-size: 21px; font-weight: 800; color: var(--brand-yellow); }
  .block-copy {
    position: absolute; left: 58px; top: 227px; width: 268px;
    font-size: 11.6px; line-height: 13.9px; font-weight: 500; text-align: justify; hyphens: auto;
  }

  .product-photo { position: absolute; }

  .folio { position: absolute; bottom: 30px; font-size: 9px; font-weight: 700; letter-spacing: 0.2px; }
  .folio-number { left: 58px; }
  .folio-url { left: 122px; }
</style>
</head>
<body>
<main class="board">
  <p class="spread-label" style="left:38px;">Inside</p>
  <p class="spread-label" style="left:613px;">Inside</p>

  <!-- Page 7 -->
  <div class="page-holder" style="left:36px;">
    <article class="page">
      <svg class="page-art" viewBox="0 0 684 970" aria-hidden="true">
        <defs>
          <linearGradient id="fold-shade-a" x1="0" y1="0" x2="1" y2="1">
            <stop offset="0" stop-color="#f7f7f7"/><stop offset="1" stop-color="#ffffff"/>
          </linearGradient>
          <linearGradient id="band-shade-a" x1="0" y1="0" x2="1" y2="1">
            <stop offset="0" stop-color="#fccb05"/><stop offset="0.6" stop-color="#f4c30a"/><stop offset="1" stop-color="#fccb05"/>
          </linearGradient>
        </defs>
        <rect width="684" height="970" fill="url(#fold-shade-a)"/>
        <polyline points="684,88 512,258 684,430" fill="none" stroke="var(--brand-yellow)" stroke-width="1.3"/>
        <polyline points="0,393 137,530 0,667" fill="none" stroke="var(--brand-yellow)" stroke-width="1.3"/>
        <polygon points="0,668 105,668 455,316 684,545 684,970 0,970" fill="url(#band-shade-a)"/>
        <polygon points="503,364 790,650 485,940 212,660" fill="var(--paper)"/>
        <polygon points="684,848 560,970 684,970" fill="#f3f3f3"/>
      </svg>

      <div class="section-tab"></div>
      <p class="section-name">OUR STOCK</p>
      <div class="brand"><span class="brand-mark"></span><span class="brand-name">Brightline Energy</span></div>

      <h1 class="page-title">PRIME GENERATORS</h1>
      <h2 class="block-heading">CONTROLLERS</h2>
      <p class="block-copy">Fugiant pelluptatis rempe nectibea nati nobitate voluptatur, verum dolorerrum velectur, ut fugit aut aborporepe volluptatem in pro beatios molendi genihillis non nonsequ aersped estius seque volupis es sanis ad que volupta quamus ipic te videndene solum esercid que re audam, nonem es atempos re nim cus et volorument fuga. Da am fugia ipidel maios everum ut venient officit quidi ut quo</p>

      <div class="product-photo" role="img" aria-label="Trailer-mounted white and black diesel generator set on a dual-axle trailer"
           style="left:340px; top:500px; width:330px; height:305px; background:linear-gradient(180deg, var(--photo-light) 0%, #d4d4d4 55%, var(--photo-dark) 100%); border-radius:6px;"></div>

      <p class="folio folio-number">7</p>
      <p class="folio folio-url">WWW.BRIGHTLINEENERGYCO.EXAMPLE</p>
    </article>
  </div>

  <!-- Page 8 -->
  <div class="page-holder" style="left:611px;">
    <article class="page">
      <svg class="page-art" viewBox="0 0 684 970" aria-hidden="true">
        <defs>
          <linearGradient id="fold-shade-b" x1="0" y1="0" x2="1" y2="1">
            <stop offset="0" stop-color="#f7f7f7"/><stop offset="1" stop-color="#ffffff"/>
          </linearGradient>
          <linearGradient id="band-shade-b" x1="0" y1="0" x2="1" y2="1">
            <stop offset="0" stop-color="#fccb05"/><stop offset="0.6" stop-color="#f4c30a"/><stop offset="1" stop-color="#fccb05"/>
          </linearGradient>
        </defs>
        <rect width="684" height="970" fill="url(#fold-shade-b)"/>
        <polyline points="684,88 512,258 684,430" fill="none" stroke="var(--brand-yellow)" stroke-width="1.3"/>
        <polyline points="0,393 137,530 0,667" fill="none" stroke="var(--brand-yellow)" stroke-width="1.3"/>
        <polygon points="0,668 105,668 455,316 684,545 684,970 0,970" fill="url(#band-shade-b)"/>
        <polygon points="503,364 790,650 485,940 212,660" fill="var(--paper)"/>
        <polygon points="684,848 560,970 684,970" fill="#f3f3f3"/>
      </svg>

      <div class="section-tab"></div>
      <p class="section-name">OUR STOCK</p>
      <div class="brand"><span class="brand-mark"></span><span class="brand-name">Brightline Energy</span></div>

      <h1 class="page-title">RENTAL GENERATORS</h1>
      <h2 class="block-heading">CONTROLLERS</h2>
      <p class="block-copy">Fugiant pelluptatis rempe nectibea nati nobitate voluptatur, verum dolorerrum velectur, ut fugit aut aborporepe volluptatem in pro beatios molendi genihillis non nonsequ aersped estius seque volupis es sanis ad que volupta quamus ipic te videndene solum esercid que re audam, nonem es atempos re nim cus et volorument fuga. Da am fugia ipidel maios everum ut venient officit quidi ut quo</p>

      <div class="product-photo" role="img" aria-label="Black industrial alternator with cooling fan housing"
           style="left:351px; top:510px; width:285px; height:290px; background:radial-gradient(circle at 45% 45%, #5a5a5a 0%, var(--photo-dark) 60%, #151515 100%); border-radius:8px;"></div>

      <p class="folio folio-number">8</p>
      <p class="folio folio-url">WWW.BRIGHTLINEENERGYCO.EXAMPLE</p>
    </article>
  </div>
</main>
</body>
</html>
```